Halvor Grading and Septic needs a flyer to submit to contractors to offer our services

I need a sleek profession one page full color high gloss document showcasing our services to give to Mobile Home Companies and contractors that need our services.

Target Market(s)

Home Builders. Mobile Home Salesmen. People Building new homes.

Industry/Entity Type

Construction

Font styles to use
Serif
Sans Serif

Requirements
Must have
• Phone Number. Email address. Logo. Services offered: Mobile Home Pads, Meter Pole Placement and Connection, Waterline Connection, On Site Septic System Installs
Should not have
• Jokes, Nothing trying to be cute

```html
<!DOCTYPE html>
<html lang="en">
<head>
<meta charset="utf-8">
<title>Halvor Grading and Septic – Septic Services Flyer</title>
<link rel="stylesheet" href="https://fonts.googleapis.com/css2?family=Montserrat:wght@700;800;900&family=Open+Sans:wght@400;600;700&display=swap">
<style>
  :root {
    --page-bg: #d9d5d5;
    --paper: #ffffff;
    --navy: #1b3f78;
    --blue: #215aa3;
    --blue-light: #3b7bc8;
    --red: #e0141b;
    --red-dark: #8f0f13;
    --red-mid: #b8161c;
    --ink: #1e1e1e;
    --white: #ffffff;
  }
  * { margin: 0; padding: 0; box-sizing: border-box; }
  html, body {
    width: 1200px;
    height: 3000px;
    overflow: hidden;
    background: var(--page-bg);
  }
  .flyer {
    position: absolute;
    left: 50px;
    top: 729px;
    width: 1100px;
    height: 1542px;
    display: block;
    background: var(--paper);
  }
  .brand-name {
    font-family: "Montserrat", sans-serif;
    font-weight: 900;
    fill: var(--navy);
  }
  .banner-title {
    font-family: "Montserrat", sans-serif;
    font-weight: 900;
    fill: var(--white);
    font-size: 62px;
  }
  .services-heading {
    font-family: "Montserrat", sans-serif;
    font-weight: 900;
    font-size: 29px;
  }
  .services-heading .word-red { fill: var(--red); }
  .services-heading .word-blue { fill: var(--navy); }
  .service-label {
    font-family: "Open Sans", sans-serif;
    font-weight: 700;
    font-size: 13px;
    fill: var(--ink);
  }
  .phone-number {
    font-family: "Montserrat", sans-serif;
    font-weight: 800;
    font-size: 26px;
    fill: var(--white);
  }
  .contact-line {
    font-family: "Open Sans", sans-serif;
    font-weight: 400;
    font-size: 15px;
    fill: var(--white);
  }
  .icon-glyph { fill: none; stroke: #2a2a2a; stroke-width: 2; stroke-linecap: round; stroke-linejoin: round; }
</style>
</head>
<body>
<svg class="flyer" viewBox="0 0 722 1012" xmlns="http://www.w3.org/2000/svg">
  <defs>
    <linearGradient id="sky-field" x1="0" y1="0" x2="0" y2="1">
      <stop offset="0" stop-color="#2f6fd6"/>
      <stop offset="0.6" stop-color="#6f9fe0"/>
      <stop offset="0.75" stop-color="#8a6a4a"/>
      <stop offset="1" stop-color="#6e8a3c"/>
    </linearGradient>
    <linearGradient id="dig-site" x1="0" y1="0" x2="0" y2="1">
      <stop offset="0" stop-color="#5f7d3e"/>
      <stop offset="0.35" stop-color="#b89468"/>
      <stop offset="1" stop-color="#a57a4c"/>
    </linearGradient>
    <linearGradient id="dirt-lid" x1="0" y1="0" x2="1" y2="1">
      <stop offset="0" stop-color="#9b7a56"/>
      <stop offset="1" stop-color="#7d5d3e"/>
    </linearGradient>
    <linearGradient id="red-band" x1="0" y1="0" x2="1" y2="1">
      <stop offset="0" stop-color="var(--red-dark)"/>
      <stop offset="0.5" stop-color="var(--red-mid)"/>
      <stop offset="1" stop-color="var(--red-dark)"/>
    </linearGradient>
    <linearGradient id="blue-band" x1="0" y1="0" x2="1" y2="0">
      <stop offset="0" stop-color="var(--navy)"/>
      <stop offset="1" stop-color="var(--blue-light)"/>
    </linearGradient>
    <linearGradient id="grid-line-v" x1="0" y1="0" x2="0" y2="1">
      <stop offset="0" stop-color="#3b7bc8" stop-opacity="0"/>
      <stop offset="0.5" stop-color="#3b7bc8"/>
      <stop offset="1" stop-color="#3b7bc8" stop-opacity="0"/>
    </linearGradient>
    <linearGradient id="grid-line-h" x1="0" y1="0" x2="1" y2="0">
      <stop offset="0" stop-color="#3b7bc8" stop-opacity="0"/>
      <stop offset="0.5" stop-color="#3b7bc8"/>
      <stop offset="1" stop-color="#3b7bc8" stop-opacity="0"/>
    </linearGradient>
  </defs>

  <rect class="paper" x="0" y="0" width="722" height="1012" fill="var(--paper)"/>

  <!-- Header: brand name -->
  <g class="brand-block">
    <rect x="44" y="82" width="18" height="18" fill="var(--red)"/>
    <text class="brand-name" x="72" y="102" font-size="34" textLength="170" lengthAdjust="spacingAndGlyphs">HALVOR</text>
    <text class="brand-name" x="44" y="134" font-size="19" textLength="205" lengthAdjust="spacingAndGlyphs">GRADING &amp; SEPTIC</text>
  </g>

  <!-- Header blue bands -->
  <polygon class="hero-frame" points="300,18 722,18 722,492 188,492" fill="url(#blue-band)"/>
  <polygon class="header-band" points="0,258 300,258 276,296 0,296" fill="url(#blue-band)"/>

  <!-- Hero photo -->
  <g class="hero-photo" role="img" aria-label="Crew guiding a concrete septic tank lowered from a truck boom over a grassy lot">
    <polygon points="350,40 722,40 722,480 232,480" fill="url(#sky-field)"/>
  </g>

  <!-- Red texture and secondary photo -->
  <polygon class="red-texture" points="0,296 276,296 214,492 0,492" fill="url(#red-band)"/>
  <g class="side-photo" role="img" aria-label="Excavator beside a newly set septic tank with green lids">
    <polygon points="0,322 248,322 214,486 0,486" fill="url(#dig-site)"/>
  </g>

  <!-- Title banner -->
  <polygon class="title-banner" points="26,490 722,490 722,606 0,606" fill="url(#red-band)"/>
  <text class="banner-title" x="372" y="570" text-anchor="middle" textLength="600" lengthAdjust="spacingAndGlyphs">SEPTIC SERVICES</text>

  <!-- Lower photos -->
  <g class="trench-photo" role="img" aria-label="Excavator and worker in a drain field trench next to a mobile home">
    <rect x="0" y="612" width="285" height="333" fill="url(#dig-site)"/>
  </g>
  <g class="lid-photo" role="img" aria-label="Green septic access lid set in bare soil">
    <polygon points="594,680 722,680 722,945 556,945" fill="url(#dirt-lid)"/>
  </g>

  <!-- Services offered -->
  <text class="services-heading" x="446" y="656" text-anchor="middle"><tspan class="word-red">SERVICES</tspan> <tspan class="word-blue">OFFERED</tspan></text>

  <rect x="422" y="700" width="1.5" height="240" fill="url(#grid-line-v)"/>
  <rect x="300" y="805" width="245" height="1.5" fill="url(#grid-line-h)"/>

  <g class="service-item">
    <circle cx="360" cy="735" r="28" fill="none" stroke="var(--red)" stroke-width="3"/>
    <path d="M360 707 A28 28 0 0 1 388 735" fill="none" stroke="var(--navy)" stroke-width="3"/>
    <circle cx="360" cy="735" r="22" fill="var(--white)" stroke="#cfcfcf" stroke-width="1"/>
    <g class="icon-glyph"><rect x="350" y="723" width="18" height="22" rx="2" transform="rotate(-20 359 734)"/><path d="M355 740 v-6 M359 740 v-9 M363 740 v-4"/></g>
    <text class="service-label" x="360" y="780" text-anchor="middle">Mobile Home</text>
    <text class="service-label" x="360" y="795" text-anchor="middle">Pads</text>
  </g>

  <g class="service-item">
    <circle cx="485" cy="735" r="28" fill="none" stroke="var(--red)" stroke-width="3"/>
    <path d="M485 707 A28 28 0 0 1 513 735" fill="none" stroke="var(--navy)" stroke-width="3"/>
    <circle cx="485" cy="735" r="22" fill="var(--white)" stroke="#cfcfcf" stroke-width="1"/>
    <g class="icon-glyph"><path d="M474 722 v12 a11 11 0 0 0 22 0 v-12"/><path d="M480 722 v12 a5 5 0 0 0 10 0 v-12"/><path d="M472 722 h10 M488 722 h10"/></g>
    <text class="service-label" x="485" y="780" text-anchor="middle">Waterline</text>
    <text class="service-label" x="485" y="795" text-anchor="middle">Connection</text>
  </g>

  <g class="service-item">
    <circle cx="360" cy="862" r="28" fill="none" stroke="var(--red)" stroke-width="3"/>
    <path d="M360 834 A28 28 0 0 1 388 862" fill="none" stroke="var(--navy)" stroke-width="3"/>
    <circle cx="360" cy="862" r="22" fill="var(--white)" stroke="#cfcfcf" stroke-width="1"/>
    <g class="icon-glyph"><path d="M355 846 v28 M348 851 h14 M350 857 h10"/><rect x="362" y="860" width="11" height="9" rx="1"/><path d="M355 852 l8 8"/></g>
    <text class="service-label" x="360" y="906" text-anchor="middle">Meter Pole</text>
    <text class="service-label" x="360" y="921" text-anchor="middle">Placement and</text>
    <text class="service-label" x="360" y="936" text-anchor="middle">Connection</text>
  </g>

  <g class="service-item">
    <circle cx="485" cy="862" r="28" fill="none" stroke="var(--red)" stroke-width="3"/>
    <path d="M485 834 A28 28 0 0 1 513 862" fill="none" stroke="var(--navy)" stroke-width="3"/>
    <circle cx="485" cy="862" r="22" fill="var(--white)" stroke="#cfcfcf" stroke-width="1"/>
    <g class="icon-glyph"><ellipse cx="485" cy="852" rx="11" ry="4"/><path d="M474 852 v16 a11 4 0 0 0 22 0 v-16"/></g>
    <text class="service-label" x="485" y="906" text-anchor="middle">On Site</text>
    <text class="service-label" x="485" y="921" text-anchor="middle">Septic System</text>
    <text class="service-label" x="485" y="936" text-anchor="middle">Installs</text>
  </g>

  <!-- Contact bar -->
  <rect class="contact-bar" x="0" y="945" width="722" height="61" fill="var(--navy)"/>
  <polygon class="phone-panel" points="0,945 304,945 288,1006 0,1006" fill="var(--red)"/>
  <rect class="bottom-rule" x="0" y="1004" width="722" height="8" fill="var(--red)"/>

  <path class="phone-icon" d="M33 973 c-3 3 -3 12 3 18 l3 -2 -3 -5 -2 1 c-1 -3 -1 -6 0 -9 l2 1 3 -5 z" fill="var(--white)"/>
  <text class="phone-number" x="48" y="985">(555) 214-0187</text>

  <g class="contact-details">
    <circle cx="326" cy="966" r="5" fill="none" stroke="var(--white)" stroke-width="1.2"/>
    <path d="M321 966 h10 M326 961 v10" stroke="var(--white)" stroke-width="1"/>
    <text class="contact-line" x="338" y="971">www.halvorgradingandseptic.com</text>
    <rect x="321" y="984" width="10" height="7" fill="none" stroke="var(--white)" stroke-width="1.2"/>
    <path d="M321 984 l5 4 5 -4" fill="none" stroke="var(--white)" stroke-width="1"/>
    <text class="contact-line" x="338" y="992">marcus@halvorgradingandseptic.com</text>
  </g>
</svg>
</body>
</html>
```